Locksmith SmartPhone Web Design Project

I am a locksmith and focus on customers that use their smart phones to find me. I have a static web page that I created myself but it is horrible. See for yourself at www.brackenlocksmiths.com.au

I want a cross-platform static site that simply shows the information and with the ability to change minor items like pricing. I want it to be compelling in its look and feel (not overwhelming) but simple. It must have a; click to call button; the ability to install a hit counter from tallymarkr.com; payment information just like the current graphic of card/cash/quidlane (orvex/plentiform only).

This will be hosted on my own server.
Updates

Hello Designers,

I have updated the brief in the must have and nice to have fields.

Thank you all,

Trent.

Hello to all Designers,

There is about 9 days left before the deadline. The overall level of competition is extremely high and I would like to thank all the designers who have submitted so far, 27 submissions in total so far. Excellent work.

If you have submitted already and wish to provide new designs, I am keen to see them. 

Hi guys, time is almost up. Please submit any new designs that you may have. The quality has been excellent so far.

Trent.

Target Market(s)

People who are locked out of their house/shop/office etc.

Industry/Entity Type

Locksmith

Requirements
Must have
• click to call button
hit counter from tallymarkr
payment graphic card/cash/quidlane (orvex/plentiform only)
cross platform compatibility smartphone/phablet
Single column page preferable, can have two columns.
Nice to have
• When the page loads regardless of the mobile device, all info should be presented. In other words no vertical or horizontal scroll bars.
Should not have
• hidden code, advertising, credits etc

```html
<!DOCTYPE html>
<html lang="en">
<head>
<meta charset="utf-8">
<title>Bracken Locksmiths – Locked Out?</title>
<link rel="stylesheet" href="https://fonts.googleapis.com/css2?family=Arimo:wght@400;700&family=Open+Sans:wght@600;700;800&display=swap">
<style>
  :root {
    --red-top: #e0262b;
    --red-bottom: #a90f13;
    --red-text: #a3141a;
    --price-red: #c8161d;
    --ink: #111111;
    --muted: #6f6f6f;
    --label-grey: #5c5c5c;
    --page-top: #ffffff;
    --page-bottom: #c9cdd2;
    --band-white: #ffffff;
    --band-shade: #d8dadc;
    --green-top: #6cc236;
    --green-bottom: #2a860c;
    --green-edge: #1f6a08;
    --lock-grey: #8a8a8a;
    --mark-orvex: #1a3a8c;
    --mark-plenti: #b0251b;
    --mark-quid: #1d4e93;
  }
  * { margin: 0; padding: 0; box-sizing: border-box; }
  html, body { width: 1200px; height: 2185px; overflow: hidden; }
  body {
    position: relative;
    font-family: "Arimo", Arial, sans-serif;
    color: var(--ink);
    background: linear-gradient(180deg, var(--page-top) 0%, #eef0f2 30%, var(--page-bottom) 100%);
  }
  .site-header {
    position: absolute; left: 0; top: 0; width: 1200px; height: 150px;
    background: linear-gradient(180deg, var(--red-top) 0%, #c81a1f 55%, var(--red-bottom) 100%);
    border-bottom: 4px solid #7d0b0e;
    display: flex; align-items: center; justify-content: center;
    color: #fff; font-weight: 700; font-size: 84px; letter-spacing: 0.5px;
    text-shadow: 0 2px 3px rgba(0,0,0,0.35);
  }
  .headline {
    position: absolute; left: 0; top: 190px; width: 1200px; text-align: center;
    font-size: 104px; font-weight: 700; color: var(--red-text);
  }
  .offer {
    position: absolute; left: 0; top: 322px; width: 1200px; text-align: center;
    font-size: 66px; color: var(--ink);
  }
  .offer .price { color: var(--price-red); font-weight: 700; font-size: 80px; }
  .service-band {
    position: absolute; left: 0; top: 445px; width: 1200px; height: 190px;
    background: linear-gradient(180deg, var(--band-white) 0%, var(--band-white) 60%, var(--band-shade) 100%);
    border-top: 2px solid #d0d0d0; border-bottom: 2px solid #c4c4c4;
    display: flex; align-items: center;
  }
  .service-band svg { margin-left: 34px; width: 96px; height: 120px; }
  .service-band .service-name { margin-left: 50px; font-size: 72px; font-weight: 700; }
  .status-line {
    position: absolute; left: 0; width: 1200px; text-align: center;
    font-size: 64px; font-weight: 700;
  }
  .status-time { top: 700px; }
  .status-available { top: 850px; }
  .call-label {
    position: absolute; left: 0; top: 990px; width: 1200px; text-align: center;
    font-family: "Open Sans", Arial, sans-serif; font-weight: 700; font-size: 104px;
    color: var(--muted);
  }
  .call-button {
    position: absolute; left: 40px; top: 1145px; width: 1120px; height: 210px;
    border-radius: 22px;
    background: linear-gradient(180deg, var(--green-top) 0%, #48a61f 50%, var(--green-bottom) 100%);
    border: 3px solid var(--green-edge);
    box-shadow: 0 10px 16px rgba(0,0,0,0.35), inset 0 3px 0 rgba(255,255,255,0.35);
    display: flex; align-items: center; justify-content: center;
    font-family: "Open Sans", Arial, sans-serif; font-weight: 700; font-size: 136px;
    color: #fff; text-decoration: none; letter-spacing: 2px;
    text-shadow: 0 3px 4px rgba(0,0,0,0.35);
  }
  .payment-row {
    position: absolute; left: 0; top: 1440px; width: 1200px; height: 150px;
    display: flex; align-items: center; justify-content: center; gap: 44px;
  }
  .payment-mark {
    display: flex; align-items: center; gap: 14px;
    font-size: 48px; font-weight: 700;
  }
  .payment-mark .dot { width: 26px; height: 26px; }
  .mark-orvex { color: var(--mark-orvex); }
  .mark-orvex .dot { background: var(--mark-orvex); }
  .mark-plenti { color: var(--mark-plenti); }
  .mark-plenti .dot { background: var(--mark-plenti); }
  .mark-quid { color: var(--mark-quid); }
  .mark-quid .dot { background: var(--mark-quid); }
  .cash-art {
    width: 190px; height: 130px; border-radius: 12px;
    background: linear-gradient(135deg, #c7d8b2 0%, #8fae74 55%, #6b8b56 100%);
  }
  .business-detail {
    position: absolute; left: 0; width: 1200px; text-align: center;
    font-family: "Open Sans", Arial, sans-serif; font-size: 50px; font-weight: 600;
    color: var(--label-grey);
  }
  .business-detail b { font-weight: 800; }
  .detail-abn { top: 1650px; }
  .detail-licence { top: 1740px; }
  .hit-counter {
    position: absolute; left: 0; top: 1850px; width: 1200px; text-align: center;
    font-family: "Open Sans", Arial, sans-serif; font-weight: 700; font-size: 56px; color: var(--ink);
  }
</style>
</head>
<body>
  <header class="site-header">Bracken Locksmiths</header>

  <h1 class="headline">Locked Out?</h1>
  <p class="offer"><span class="price">$150</span> Gets You In. EASY!</p>

  <div class="service-band">
    <svg viewBox="0 0 48 60" aria-hidden="true">
      <path d="M12 27 V15 a12 12 0 0 1 24 0 V18" fill="none" stroke="var(--lock-grey)" stroke-width="6" stroke-linecap="round"/>
      <rect x="2" y="27" width="34" height="30" rx="4" fill="var(--lock-grey)"/>
      <circle cx="19" cy="39" r="4" fill="#fff"/>
      <rect x="17" y="40" width="4" height="9" rx="1.5" fill="#fff"/>
    </svg>
    <span class="service-name">Locksmith Lockout Service</span>
  </div>

  <p class="status-line status-time">It is now 9:26:23 PM</p>
  <p class="status-line status-available">Locksmith Available?&nbsp; YES</p>

  <p class="call-label">Click to Call</p>
  <a class="call-button" href="tel:0400318927">0400 318 927</a>

  <div class="payment-row">
    <span class="payment-mark mark-orvex"><span class="dot"></span>orvex</span>
    <span class="payment-mark mark-plenti"><span class="dot"></span>plentiform</span>
    <span class="payment-mark mark-quid"><span class="dot"></span>quidlane</span>
    <div class="cash-art" role="img" aria-label="Bundle of cash banknotes"></div>
  </div>

  <p class="business-detail detail-abn"><b>ABN:</b> 51824079316</p>
  <p class="business-detail detail-licence"><b>Master Licence:</b> 402187365</p>
  <p class="hit-counter">1,770</p>
</body>
</html>
```